Small Business Broker Business Card Design

A business card design for a small business brokerage, which is a financial service, not unlike real estate brokerage, but for small businesses such as laundromats, pizza shops, restaurants, cleaners etc. The designs should all be simple, more conservative in nature, using the colors and font of the logo. Again, think real estate Brokerage as a business context
Contact Information for Business Card
Name: Glen R. Harlow. Title: Small Business Advisor. Email: g.harlow@bayfieldcapitalworks.example. Mobile: (555) 274-3918. Office: (555) 806-2147. www.bayfieldcapitalworks.example

```html
<!DOCTYPE html>
<html lang="en">
<head>
<meta charset="utf-8">
<title>Bayfield Capital Works – Business Card</title>
<link rel="stylesheet" href="https://fonts.googleapis.com/css2?family=Roboto+Condensed:wght@400;700&display=swap">
<style>
  :root {
    --page-bg: #e6e8ec;
    --card-white: #ffffff;
    --brand-green: #8cc63f;
    --brand-green-deep: #72a92b;
    --brand-navy: #173a6e;
    --ink: #1d1d1f;
    --rule: #3a3a3a;
  }
  * { box-sizing: border-box; margin: 0; padding: 0; }
  html, body { width: 1200px; height: 780px; overflow: hidden; }
  body {
    background: var(--page-bg);
    font-family: "Roboto Condensed", Arial, sans-serif;
    display: flex;
    align-items: center;
    justify-content: center;
    gap: 40px;
  }
  .card {
    position: relative;
    width: 540px;
    height: 310px;
    border-radius: 18px;
    overflow: hidden;
    box-shadow: 0 10px 26px rgba(0,0,0,.18);
  }

  /* Front */
  .card-front { background: var(--card-white); }
  .company {
    position: absolute;
    left: 34px;
    top: 70px;
    width: 205px;
    display: flex;
    align-items: center;
    gap: 10px;
  }
  .company-square {
    width: 22px; height: 22px;
    flex: none;
    background: var(--brand-green);
  }
  .company-name {
    font-weight: 700;
    font-size: 17px;
    line-height: 1.2;
    letter-spacing: .5px;
    color: var(--brand-navy);
    text-transform: uppercase;
  }
  .divider {
    position: absolute;
    left: 262px;
    top: 44px;
    width: 1px;
    height: 170px;
    background: var(--rule);
  }
  .contact {
    position: absolute;
    left: 282px;
    top: 52px;
    width: 245px;
  }
  .person-name {
    font-weight: 700;
    font-size: 30px;
    line-height: 1;
    color: var(--brand-green);
  }
  .person-title {
    font-size: 14px;
    color: var(--ink);
    margin-top: 4px;
    margin-bottom: 14px;
  }
  .contact-line {
    display: flex;
    align-items: center;
    gap: 7px;
    font-size: 13px;
    color: var(--ink);
    line-height: 1.55;
    white-space: nowrap;
  }
  .contact-line svg { width: 12px; height: 12px; flex: none; }
  .web-band {
    position: absolute;
    left: 0;
    bottom: 0;
    width: 410px;
    height: 50px;
    background: var(--brand-green);
    display: flex;
    align-items: center;
    gap: 8px;
    padding-left: 42px;
    color: #fff;
    font-size: 15px;
  }
  .web-band svg { width: 14px; height: 14px; flex: none; }
  .corner-block {
    position: absolute;
    right: 0;
    bottom: 0;
    width: 52px;
    height: 50px;
    background: var(--brand-navy);
  }

  /* Back */
  .card-back {
    background: var(--brand-green);
    display: flex;
    align-items: center;
    justify-content: center;
  }
  .back-name {
    font-weight: 700;
    font-size: 26px;
    letter-spacing: 1px;
    text-transform: uppercase;
    color: var(--brand-green-deep);
  }
</style>
</head>
<body>

  <section class="card card-front" aria-label="Business card front">
    <div class="company">
      <span class="company-square"></span>
      <span class="company-name">Bayfield Capital<br>Works, Inc</span>
    </div>

    <div class="divider"></div>

    <div class="contact">
      <p class="person-name">Glen R. Harlow</p>
      <p class="person-title">Small Business Advisor</p>
      <p class="contact-line">
        <svg viewBox="0 0 12 12" aria-hidden="true"><rect x="3" y="1" width="6" height="10" rx="1" fill="none" stroke="#173a6e" stroke-width="1.4"/></svg>
        (555) 274-3918
      </p>
      <p class="contact-line">
        <svg viewBox="0 0 12 12" aria-hidden="true"><path d="M3 1.5l2 2-1.2 1.4a6 6 0 0 0 3.3 3.3L8.5 7l2 2-1.5 1.5C5 10.5 1.5 7 1.5 3z" fill="#8cc63f"/></svg>
        (555) 806-2147
      </p>
      <p class="contact-line">
        <svg viewBox="0 0 12 12" aria-hidden="true"><rect x="1" y="2.5" width="10" height="7" fill="#8cc63f"/><path d="M1 2.5l5 4 5-4" fill="none" stroke="#fff" stroke-width="1"/></svg>
        g.harlow@bayfieldcapitalworks.example
      </p>
    </div>

    <div class="web-band">
      <svg viewBox="0 0 14 14" aria-hidden="true"><circle cx="7" cy="7" r="6" fill="none" stroke="#fff" stroke-width="1.3"/><ellipse cx="7" cy="7" rx="2.6" ry="6" fill="none" stroke="#fff" stroke-width="1"/><path d="M1 7h12" stroke="#fff" stroke-width="1"/></svg>
      www.bayfieldcapitalworks.example
    </div>
    <div class="corner-block"></div>
  </section>

  <section class="card card-back" aria-label="Business card back">
    <span class="back-name">Bayfield Capital Works, Inc</span>
  </section>

</body>
</html>
```